Construction business card

I need a new business card, they can connect with my logo, brand.
What we do is residential house , design and build
I like: Navy blue / black
I attached our logo, brand,
and, some idea for business card.

```html
<!DOCTYPE html>
<html lang="en">
<head>
<meta charset="UTF-8">
<title>Harbourline Building Group – Business Card</title>
<link rel="stylesheet" href="https://fonts.googleapis.com/css2?family=Arimo:wght@400;700&family=Varela+Round&display=swap">
<style>
  :root {
    --backdrop: #d3e9ea;
    --card-white: #ffffff;
    --navy-deep: #020a26;
    --navy-mid: #0b1c45;
    --brand-blue: #3f86d0;
    --brand-blue-dark: #1e4f8f;
    --ink: #1a1a1a;
    --rule-grey: #9a9a9a;
  }
  * { box-sizing: border-box; margin: 0; padding: 0; }
  html, body { width: 1200px; height: 1200px; overflow: hidden; }
  body {
    background: var(--backdrop);
    font-family: "Arimo", Arial, sans-serif;
    color: var(--ink);
    position: relative;
  }
  .card {
    position: absolute;
    left: 150px;
    width: 900px;
    height: 514px;
    border-radius: 4px;
    box-shadow: 0 14px 36px rgba(20, 50, 60, 0.22);
    overflow: hidden;
  }
  /* Front */
  .card--front { top: 60px; background: var(--card-white); }
  .brand-mark {
    position: absolute;
    left: 70px;
    top: 86px;
    display: flex;
    align-items: center;
    gap: 18px;
  }
  .brand-mark__square {
    width: 26px; height: 26px;
    background: var(--brand-blue);
  }
  .brand-mark__name {
    font-family: "Arimo", Arial, sans-serif;
    font-weight: 700;
    font-size: 50px;
    line-height: 1.05;
    letter-spacing: 1px;
    color: var(--navy-deep);
    text-transform: uppercase;
  }
  .divider {
    position: absolute;
    left: 60px; right: 84px;
    top: 318px;
    height: 2px;
    background: var(--rule-grey);
  }
  .holder {
    position: absolute;
    right: 84px;
    top: 238px;
    text-align: right;
  }
  .holder__name {
    font-family: "Varela Round", Arial, sans-serif;
    font-size: 44px;
    color: var(--brand-blue);
    line-height: 1;
  }
  .holder__role {
    font-size: 19px;
    color: var(--ink);
    margin-top: 4px;
  }
  .contact-list {
    position: absolute;
    left: 60px;
    top: 348px;
    list-style: none;
  }
  .contact-list li {
    display: flex;
    align-items: center;
    gap: 22px;
    font-size: 23px;
    height: 40px;
  }
  .contact-list svg, .address svg { width: 24px; height: 24px; flex: none; }
  .address {
    position: absolute;
    right: 84px;
    top: 372px;
    display: flex;
    align-items: center;
    gap: 24px;
    font-size: 23px;
    line-height: 1.45;
    text-align: left;
  }
  /* Back */
  .card--back {
    top: 626px;
    background: var(--navy-deep);
  }
  .back-decoration {
    position: absolute;
    right: 0; bottom: 0;
    width: 640px; height: 380px;
    background: radial-gradient(ellipse at 65% 55%, rgba(63,134,208,0.45), rgba(30,79,143,0.18) 50%, rgba(2,10,38,0) 75%);
  }
  .back-brand {
    position: absolute;
    left: 90px;
    top: 90px;
    display: flex;
    align-items: center;
    gap: 18px;
  }
  .back-brand .brand-mark__name { color: var(--card-white); }
</style>
</head>
<body>

<section class="card card--front" aria-label="Business card front">
  <div class="brand-mark">
    <span class="brand-mark__square"></span>
    <span class="brand-mark__name">Harbourline<br>Building Group</span>
  </div>

  <div class="holder">
    <p class="holder__name">Sam Carter</p>
    <p class="holder__role">Manager</p>
  </div>

  <div class="divider"></div>

  <ul class="contact-list">
    <li>
      <svg viewBox="0 0 24 24" aria-hidden="true"><path fill="var(--brand-blue)" d="M6.6 10.8a15.1 15.1 0 0 0 6.6 6.6l2.2-2.2a1 1 0 0 1 1-.25 11.4 11.4 0 0 0 3.6.57 1 1 0 0 1 1 1V20a1 1 0 0 1-1 1A17 17 0 0 1 3 4a1 1 0 0 1 1-1h3.5a1 1 0 0 1 1 1c0 1.25.2 2.45.57 3.6a1 1 0 0 1-.25 1z"/></svg>
      <span>0400 318 527</span>
    </li>
    <li>
      <svg viewBox="0 0 24 24" aria-hidden="true"><rect x="2" y="5" width="20" height="14" rx="1.5" fill="var(--brand-blue)"/><path d="M3 6l9 7 9-7" fill="none" stroke="#fff" stroke-width="1.6"/></svg>
      <span>info@harbourlinebuild.com.au</span>
    </li>
    <li>
      <svg viewBox="0 0 24 24" aria-hidden="true"><g fill="none" stroke="var(--brand-blue)" stroke-width="1.6"><circle cx="12" cy="12" r="9.5"/><ellipse cx="12" cy="12" rx="4.2" ry="9.5"/><path d="M2.5 12h19M4 7h16M4 17h16"/></g></svg>
      <span>www.harbourlinebuild.com.au</span>
    </li>
  </ul>

  <div class="address">
    <span>48 Wattle Grove Road,<br>Bayside Park, Vic 3190</span>
    <svg viewBox="0 0 24 24" aria-hidden="true"><path fill="var(--brand-blue)" d="M12 2a7 7 0 0 0-7 7c0 5 7 13 7 13s7-8 7-13a7 7 0 0 0-7-7z"/><circle cx="12" cy="9" r="2.6" fill="#fff"/></svg>
  </div>
</section>

<section class="card card--back" aria-label="Business card back">
  <div class="back-decoration" role="img" aria-label="Large blue roofline graphic on navy"></div>
  <div class="back-brand brand-mark">
    <span class="brand-mark__square"></span>
    <span class="brand-mark__name">Harbourline<br>Building Group</span>
  </div>
</section>

</body>
</html>
```